Home Security Company Business Card

Looking for a eye catching business card that is non traditional and stands out but yet still looks professional. It should include all the pertinent information such as name, title, address, telephone, e-mail, website address should definitely stand out and then finally the logo.

Target Market(s)

Residential and Commercial accounts mostly upscale accounts

Industry/Entity Type

Security

Contact Information for Business Card

Name
Title
Address
Office #
Cell #
E-mail
Website

Font styles to use
Serif
Sans Serif

Requirements
Must have
• Logo, two sided color configuration
Nice to have
• You decide
Should not have
• There really aren't any.

```html
<!DOCTYPE html>
<html lang="en">
<head>
<meta charset="utf-8">
<title>Harborline Security Group – Business Card</title>
<link href="https://fonts.googleapis.com/css2?family=Open+Sans:ital,wght@0,400;0,600;0,700;1,400&display=swap" rel="stylesheet">
<style>
  :root {
    --stage: #3a3a3a;
    --maroon: #730d00;
    --gold: #d39a3c;
    --gold-deep: #b9792a;
    --paper: #f8f8f8;
    --ink: #3d3d3d;
    --white: #ffffff;
  }
  * { margin: 0; padding: 0; box-sizing: border-box; }
  html, body { width: 1200px; height: 750px; overflow: hidden; }
  body {
    background: var(--stage);
    font-family: "Open Sans", Arial, sans-serif;
    position: relative;
  }
  .card {
    position: absolute;
    top: 228px;
    width: 460px;
    height: 262px;
    overflow: hidden;
  }
  .card--front { left: 144px; background: var(--maroon); }
  .card--back { left: 612px; background: var(--maroon); }

  .front-shape { position: absolute; inset: 0; }

  .brand-dot {
    position: absolute;
    left: 42px; top: 68px;
    width: 54px; height: 54px;
    border-radius: 50%;
    background: var(--gold);
  }
  .company-name {
    position: absolute;
    left: 114px; top: 80px;
    font-weight: 700;
    font-size: 14px;
    line-height: 16px;
    color: var(--maroon);
    width: 150px;
  }
  .address {
    position: absolute;
    left: 114px; top: 120px;
    font-size: 11px;
    line-height: 14px;
    color: var(--ink);
  }
  .contact-list {
    position: absolute;
    left: 114px; top: 157px;
    list-style: none;
  }
  .contact-list li {
    display: flex;
    align-items: center;
    height: 17.7px;
    font-size: 11px;
    color: var(--ink);
  }
  .contact-list svg { width: 11px; height: 11px; margin-right: 6px; fill: var(--maroon); }

  .person {
    position: absolute;
    right: 77px; top: 84px;
    text-align: right;
  }
  .person-name {
    font-weight: 600;
    font-size: 16px;
    line-height: 20px;
    color: var(--maroon);
  }
  .person-title {
    font-size: 12px;
    line-height: 15px;
    color: var(--gold-deep);
  }

  .back-brand {
    position: absolute;
    left: 0; right: 0; top: 112px;
    text-align: center;
    font-weight: 700;
    font-size: 20px;
    color: var(--gold);
  }
  .back-web {
    position: absolute;
    left: 0; right: 0; top: 216px;
    text-align: center;
    font-style: italic;
    font-size: 11px;
    letter-spacing: 3px;
    color: var(--white);
  }
</style>
</head>
<body>

  <section class="card card--front">
    <svg class="front-shape" viewBox="0 0 460 262" width="460" height="262">
      <defs>
        <linearGradient id="goldSweep" x1="0" y1="1" x2="1" y2="0">
          <stop offset="0" stop-color="#c98a34"/>
          <stop offset="0.6" stop-color="#d9a24a"/>
          <stop offset="1" stop-color="#b06e22"/>
        </linearGradient>
      </defs>
      <path d="M0 0 H362 C414 34 440 112 420 172 C406 212 384 240 362 262 H0 Z" fill="var(--paper)"/>
      <path d="M238 262 C318 240 400 196 418 104 C430 168 404 226 358 262 Z" fill="url(#goldSweep)"/>
    </svg>

    <div class="brand-dot"></div>
    <div class="company-name">Harborline Security Group</div>

    <p class="address">1420 Cedar Ridge Road<br>Juneau, Alaska 99801</p>

    <ul class="contact-list">
      <li>
        <svg viewBox="0 0 12 12"><path d="M2.5 0.5 L4.5 3 L3.4 4.3 C4 5.8 5.4 7.3 7.2 8.3 L8.5 7.2 L11.3 9 L10 11.4 C5.6 11 1.2 6.6 0.6 2 Z"/></svg>
        555 214 0187
      </li>
      <li>
        <svg viewBox="0 0 12 12"><path d="M3 0 H9 V12 H3 Z M4 1.2 V9.4 H8 V1.2 Z M5.4 10.2 H6.6 V11.2 H5.4 Z"/></svg>
        555 308 6621
      </li>
      <li>
        <svg viewBox="0 0 12 12"><path d="M0 2 H12 V10 H0 Z M1 3 L6 6.6 L11 3 Z"/></svg>
        hello@harborline.com
      </li>
      <li>
        <svg viewBox="0 0 12 12"><circle cx="6" cy="6" r="6"/><path d="M3 3 C5 4 6 3 7 2 C8 4 9 5 9 7 C7 7 6 9 5 10 C4 8 2 7 3 3 Z" fill="#ffffff" opacity="0.7"/></svg>
        www.harborline.com
      </li>
    </ul>

    <div class="person">
      <div class="person-name">Daniel Reyes</div>
      <div class="person-title">CEO/Founder</div>
    </div>
  </section>

  <section class="card card--back">
    <div class="back-brand">Harborline Security Group</div>
    <div class="back-web">www.harborline.com</div>
  </section>

</body>
</html>
```